Help me make landing pages for my web application that are mobile friendly

I need to make 2 mobile friendly landing pages for an application. The 2 pages will be related. First I need a home page and then I need a working page. I do not want to change the color scheme or logos. Just layout and design.

```html
<!DOCTYPE html>
<html lang="en">
<head>
<meta charset="utf-8">
<title>ShiftCover – Assignments</title>
<link href="https://fonts.googleapis.com/css2?family=Inter:wght@400;500;600;700&display=swap" rel="stylesheet">
<style>
:root{
  --stage:#bcbdc2;
  --screen:#f2f2f3;
  --white:#ffffff;
  --ink:#151515;
  --muted:#444;
  --purple:#6a4ca3;
  --teal:#2aaed3;
  --teal-soft:#e3f1f8;
  --green:#5aaa1e;
  --red:#e20e0e;
  --line:#dcdcdc;
  --band:#f3f3f4;
  --pill:#ececec;
  --dark:#1f1f1f;
}
*{box-sizing:border-box;margin:0;padding:0}
html,body{width:944px;height:1200px;overflow:hidden;background:var(--stage)}
body{font-family:"Inter",sans-serif;color:var(--ink)}
.stage{position:absolute;left:0;top:0;width:1708px;height:2172px;transform:scale(.55269);transform-origin:0 0}
.abs{position:absolute}
.screen{position:absolute;width:628px;background:var(--screen);overflow:hidden}
.screen--list{left:148px;top:158px;height:1118px}
.screen--detail{left:868px;top:163px;height:1780px}
.topbar{position:absolute;left:0;top:0;width:100%;height:88px;background:var(--white);box-shadow:0 2px 6px rgba(0,0,0,.12)}
.menu{position:absolute;left:28px;top:29px;width:34px;height:24px}
.menu span{position:absolute;left:0;width:34px;height:2px;background:var(--purple)}
.brand{position:absolute;left:84px;top:22px;display:flex;align-items:center;gap:10px}
.brand-dot{width:34px;height:34px;border-radius:50%;background:var(--purple)}
.brand-name{font-size:30px;font-weight:500;color:var(--teal)}
.page-title{position:absolute;left:0;width:100%;top:124px;text-align:center;font-size:28px;font-weight:700;letter-spacing:.3px}
/* assignment card */
.card{position:absolute;left:26px;width:582px;height:250px;background:var(--white);border-radius:16px;box-shadow:0 1px 4px rgba(0,0,0,.05)}
.avatar{position:absolute;left:36px;top:24px;width:106px;height:106px;border-radius:50%}
.avatar--photo-a{background:radial-gradient(circle at 50% 40%,#e0b58f,#9a7b5e 60%,#5f6a58)}
.avatar--photo-b{background:radial-gradient(circle at 50% 40%,#c99a79,#8a6b4f 60%,#767676)}
.avatar--initials{background:var(--teal);color:#fff;font-size:26px;font-weight:600;display:flex;align-items:center;justify-content:center}
.person{position:absolute;left:170px;top:22px;font-size:24px;font-weight:500}
.role{position:absolute;left:170px;top:60px;font-size:19px}
.status{position:absolute;display:flex;align-items:center;height:32px;background:var(--pill);border-radius:16px;font-size:14px}
.status .lead{display:flex;align-items:center;gap:7px;padding:0 12px 0 13px}
.status .tag{height:32px;border-radius:16px;color:#fff;font-size:15px;padding:0 12px;display:flex;align-items:center}
.tag--complete{background:var(--purple)}
.tag--active{background:var(--green)}
.tag--canceled{background:var(--red)}
.card .status{left:170px;top:99px}
.card .rule{position:absolute;left:0;right:0;top:157px;height:1px;background:var(--line)}
.meta-icon{position:absolute;width:34px;height:34px;border-radius:50%;background:var(--teal-soft);display:flex;align-items:center;justify-content:center;top:183px}
.meta-label{position:absolute;top:181px;font-size:15px}
.meta-value{position:absolute;top:201px;font-size:14px}
.edit{position:absolute;left:533px;top:202px;width:40px;height:40px;border-radius:50%;background:#eeeeee;display:flex;align-items:center;justify-content:center}
/* detail panels */
.panel{position:absolute;left:24px;width:582px;background:var(--white);border-radius:16px;overflow:hidden;box-shadow:0 1px 4px rgba(0,0,0,.06)}
.panel-head{height:46px;background:var(--band);padding:12px 20px 0;font-size:19px;font-weight:500;color:var(--purple)}
.row-icon{position:absolute;left:26px;width:36px;height:36px;border-radius:50%;background:var(--teal);display:flex;align-items:center;justify-content:center}
.row-label{position:absolute;left:79px;font-size:18px;font-weight:500}
.row-value{position:absolute;left:80px;font-size:19px}
.row-rule{position:absolute;left:14px;width:544px;height:1px;background:var(--line)}
.desc{position:absolute;left:80px;top:521px;width:480px;font-size:13.6px;line-height:18.5px}
.field{position:absolute;border:1px solid #bdbdbd;border-radius:6px;background:#fff;font-size:14px;padding:0 16px;display:flex;align-items:center;justify-content:space-between}
.textarea{align-items:flex-start;padding-top:18px}
.btn{position:absolute;height:36px;border-radius:18px;display:flex;align-items:center;justify-content:center;gap:7px;font-size:15px;font-weight:500;color:#fff}
.btn--purple{background:var(--purple)}
.btn--teal{background:var(--teal)}
.btn--ghost{background:#fff;color:var(--purple);border:1px solid var(--purple)}
.btn--dark{background:var(--dark)}
.slot-box{position:absolute;left:29px;top:123px;width:532px;height:236px;background:var(--band);border-radius:16px}
.small-label{position:absolute;font-size:14px}
</style>
</head>
<body>
<div class="stage">

  <!-- list screen -->
  <section class="screen screen--list">
    <header class="topbar">
      <div class="menu"><span style="top:0"></span><span style="top:11px"></span><span style="top:22px"></span></div>
      <div class="brand"><div class="brand-dot"></div><div class="brand-name">ShiftCover</div></div>
    </header>
    <h1 class="page-title">MY ASSIGNMENTS</h1>

    <article class="card" style="top:198px">
      <div class="avatar avatar--photo-a" role="img" aria-label="Portrait photo of Nora Hale"></div>
      <div class="person">Nora Hale</div>
      <div class="role">Teacher</div>
      <div class="status"><span class="lead"><svg width="16" height="16" viewBox="0 0 16 16"><path d="M2 8l4 4 8-8" fill="none" stroke="#6a4ca3" stroke-width="1.6"/></svg>Status</span><span class="tag tag--complete">Complete</span></div>
      <div class="rule"></div>
      <div class="meta-icon" style="left:36px"><svg width="18" height="18" viewBox="0 0 18 18"><path d="M9 16s5-5 5-9a5 5 0 0 0-10 0c0 4 5 9 5 9z" fill="none" stroke="#6a4ca3" stroke-width="1.4"/><circle cx="9" cy="7" r="2" fill="none" stroke="#6a4ca3" stroke-width="1.4"/></svg></div>
      <div class="meta-label" style="left:85px">Location</div><div class="meta-value" style="left:85px">CBES</div>
      <div class="meta-icon" style="left:205px"><svg width="20" height="20" viewBox="0 0 20 20"><circle cx="10" cy="10" r="8" fill="none" stroke="#6a4ca3" stroke-width="1.4"/><path d="M10 5v5l3 2" fill="none" stroke="#6a4ca3" stroke-width="1.4"/></svg></div>
      <div class="meta-label" style="left:250px">Time Slots</div><div class="meta-value" style="left:250px">09/02 – 09/02 (1h 0m)</div>
      <div class="edit"><svg width="20" height="20" viewBox="0 0 20 20"><path d="M4 16l1-4 9-9 3 3-9 9z" fill="none" stroke="#6a4ca3" stroke-width="1.4"/></svg></div>
    </article>

    <article class="card" style="top:461px">
      <div class="avatar avatar--initials">OP</div>
      <div class="person">Owen Pryce</div>
      <div class="role">Teacher</div>
      <div class="status"><span class="lead"><svg width="17" height="17" viewBox="0 0 20 20"><circle cx="10" cy="10" r="8" fill="none" stroke="#5aaa1e" stroke-width="1.5"/><path d="M10 5v5l3 2" fill="none" stroke="#5aaa1e" stroke-width="1.5"/></svg>Status</span><span class="tag tag--active">Active</span></div>
      <div class="rule"></div>
      <div class="meta-icon" style="left:36px"><svg width="18" height="18" viewBox="0 0 18 18"><path d="M9 16s5-5 5-9a5 5 0 0 0-10 0c0 4 5 9 5 9z" fill="none" stroke="#6a4ca3" stroke-width="1.4"/><circle cx="9" cy="7" r="2" fill="none" stroke="#6a4ca3" stroke-width="1.4"/></svg></div>
      <div class="meta-label" style="left:85px">Location</div><div class="meta-value" style="left:85px">CBES</div>
      <div class="meta-icon" style="left:205px"><svg width="20" height="20" viewBox="0 0 20 20"><circle cx="10" cy="10" r="8" fill="none" stroke="#6a4ca3" stroke-width="1.4"/><path d="M10 5v5l3 2" fill="none" stroke="#6a4ca3" stroke-width="1.4"/></svg></div>
      <div class="meta-label" style="left:250px">Time Slots</div><div class="meta-value" style="left:250px">09/02 – 09/02 (1h 0m)</div>
      <div class="edit"><svg width="20" height="20" viewBox="0 0 20 20"><path d="M4 16l1-4 9-9 3 3-9 9z" fill="none" stroke="#6a4ca3" stroke-width="1.4"/></svg></div>
    </article>

    <article class="card" style="top:724px">
      <div class="avatar avatar--photo-b" role="img" aria-label="Portrait photo of Eli Grant"></div>
      <div class="person">Eli Grant</div>
      <div class="role">Administrator</div>
      <div class="status"><span class="lead"><svg width="16" height="16" viewBox="0 0 16 16"><path d="M3 3l10 10M13 3L3 13" stroke="#e20e0e" stroke-width="1.8"/></svg>Status</span><span class="tag tag--canceled">Canceled</span></div>
      <div class="rule"></div>
      <div class="meta-icon" style="left:36px"><svg width="18" height="18" viewBox="0 0 18 18"><path d="M9 16s5-5 5-9a5 5 0 0 0-10 0c0 4 5 9 5 9z" fill="none" stroke="#6a4ca3" stroke-width="1.4"/><circle cx="9" cy="7" r="2" fill="none" stroke="#6a4ca3" stroke-width="1.4"/></svg></div>
      <div class="meta-label" style="left:85px">Location</div><div class="meta-value" style="left:85px">CBES</div>
      <div class="meta-icon" style="left:205px"><svg width="20" height="20" viewBox="0 0 20 20"><circle cx="10" cy="10" r="8" fill="none" stroke="#6a4ca3" stroke-width="1.4"/><path d="M10 5v5l3 2" fill="none" stroke="#6a4ca3" stroke-width="1.4"/></svg></div>
      <div class="meta-label" style="left:250px">Time Slots</div><div class="meta-value" style="left:250px">09/02 – 09/02 (1h 0m)</div>
      <div class="edit"><svg width="20" height="20" viewBox="0 0 20 20"><path d="M4 16l1-4 9-9 3 3-9 9z" fill="none" stroke="#6a4ca3" stroke-width="1.4"/></svg></div>
    </article>

    <article class="card" style="top:989px">
      <div class="avatar avatar--initials">OP</div>
      <div class="person">Owen Pryce</div>
      <div class="role">Teacher</div>
      <div class="status"><span class="lead"><svg width="17" height="17" viewBox="0 0 20 20"><circle cx="10" cy="10" r="8" fill="none" stroke="#5aaa1e" stroke-width="1.5"/><path d="M10 5v5l3 2" fill="none" stroke="#5aaa1e" stroke-width="1.5"/></svg>Status</span><span class="tag tag--active">Active</span></div>
    </article>
  </section>

  <!-- detail screen -->
  <section class="screen screen--detail">
    <header class="topbar">
      <div class="menu"><span style="top:0"></span><span style="top:11px"></span><span style="top:22px"></span></div>
      <div class="brand"><div class="brand-dot"></div><div class="brand-name">ShiftCover</div></div>
    </header>

    <div class="panel" style="top:125px;height:661px">
      <div class="panel-head">Opening Information</div>
      <div class="row-icon" style="top:70px"><svg width="18" height="18" viewBox="0 0 18 18"><path d="M4 2h7l3 3v11H4z M7 9h5M7 12h5" fill="none" stroke="#fff" stroke-width="1.3"/></svg></div>
      <div class="row-label" style="top:64px">Summary</div><div class="row-value" style="top:87px">Testing-test</div>
      <div class="row-rule" style="top:120px"></div>
      <div class="row-icon" style="top:135px"><svg width="18" height="18" viewBox="0 0 18 18"><path d="M9 16s5-5 5-9a5 5 0 0 0-10 0c0 4 5 9 5 9z" fill="none" stroke="#fff" stroke-width="1.3"/><circle cx="9" cy="7" r="2" fill="none" stroke="#fff" stroke-width="1.3"/></svg></div>
      <div class="row-label" style="top:130px">Location</div><div class="row-value" style="top:153px">Cedar Brook Elementary School</div>
      <div class="row-rule" style="top:191px"></div>
      <div class="row-icon" style="top:207px"><svg width="18" height="18" viewBox="0 0 18 18"><rect x="2" y="5" width="14" height="10" rx="1.5" fill="none" stroke="#fff" stroke-width="1.3"/><path d="M6 5V3h6v2M2 9h14" fill="none" stroke="#fff" stroke-width="1.3"/></svg></div>
      <div class="row-label" style="top:202px">Type</div><div class="row-value" style="top:225px">Vacancy</div>
      <div class="row-rule" style="top:263px"></div>
      <div class="row-icon" style="top:283px"><svg width="18" height="18" viewBox="0 0 18 18"><circle cx="9" cy="6" r="3" fill="none" stroke="#fff" stroke-width="1.3"/><path d="M3 16c0-4 3-5 6-5s6 1 6 5" fill="none" stroke="#fff" stroke-width="1.3"/></svg></div>
      <div class="row-label" style="top:278px">Regular Staff</div><div class="row-value" style="top:301px">Owen Pryce</div>
      <div class="row-rule" style="top:340px"></div>
      <div class="row-icon" style="top:359px"><svg width="18" height="18" viewBox="0 0 18 18"><path d="M2 9l7-7h6v6l-7 7z" fill="none" stroke="#fff" stroke-width="1.3"/><circle cx="12" cy="5.5" r="1.2" fill="#fff"/></svg></div>
      <div class="row-label" style="top:354px">Assignment Category</div><div class="row-value" style="top:377px">Teacher</div>
      <div class="row-rule" style="top:412px"></div>
      <div class="row-icon" style="top:427px"><svg width="18" height="18" viewBox="0 0 18 18"><circle cx="9" cy="4" r="2" fill="none" stroke="#fff" stroke-width="1.3"/><circle cx="4" cy="14" r="2" fill="none" stroke="#fff" stroke-width="1.3"/><circle cx="14" cy="14" r="2" fill="none" stroke="#fff" stroke-width="1.3"/><path d="M9 6v3M4 12V9h10v3" fill="none" stroke="#fff" stroke-width="1.3"/></svg></div>
      <div class="row-label" style="top:422px">Department</div><div class="row-value" style="top:445px">Test</div>
      <div class="row-rule" style="top:481px"></div>
      <div class="row-icon" style="top:499px"><svg width="18" height="18" viewBox="0 0 18 18"><path d="M3 2h9v14H3z M5 6h5M5 9h5M5 12h3M15 6l-4 6" fill="none" stroke="#fff" stroke-width="1.3"/></svg></div>
      <div class="row-label" style="top:496px">Description</div>
      <p class="desc">Lorem ipsum dolor sit amet, consectetur adipiscing elit, sed do eiusmod tempor incididunt ut labore et dolore magna aliqua. Ut enim ad minim veniam, quis nostrud exercitation ullamco laboris&nbsp; nisi ut aliquip ex ea commodo consequat. Duis aute irure dolor in reprehenderit in voluptate velit esse cillum dolore eu fugiat nulla pariatur. Excepteur sint occaecat cupidatat non proident, sunt in culpa qui officia deserunt mollit anim id est laborum."</p>
    </div>

    <div class="panel" style="top:809px;height:269px">
      <div class="panel-head">Comments</div>
      <div class="field textarea" style="left:25px;top:69px;width:532px;height:121px">Write a comment or upload a file...</div>
      <div class="btn btn--purple" style="left:25px;top:209px;width:83px"><svg width="18" height="18" viewBox="0 0 18 18"><path d="M16 2L2 8l5 2 2 5z M7 10l9-8" fill="none" stroke="#fff" stroke-width="1.3"/></svg>Post</div>
      <div class="btn btn--teal" style="left:116px;top:209px;width:98px"><svg width="18" height="18" viewBox="0 0 18 18"><path d="M9 12V3M5 7l4-4 4 4M3 12v3h12v-3" fill="none" stroke="#fff" stroke-width="1.3"/></svg>Upload</div>
    </div>

    <div class="panel" style="top:1103px;height:159px">
      <div class="panel-head">Additional Details</div>
      <div class="field" style="left:25px;top:69px;width:532px;height:58px">Parking Spot</div>
    </div>

    <div class="panel" style="top:1290px;height:460px">
      <div class="panel-head">Time Slots</div>
      <div class="btn btn--purple" style="left:25px;top:71px;width:100px"><svg width="20" height="20" viewBox="0 0 20 20"><circle cx="10" cy="10" r="8" fill="none" stroke="#fff" stroke-width="1.3"/><path d="M6 10l3 3 5-6" fill="none" stroke="#fff" stroke-width="1.3"/></svg>Accept</div>
      <div class="btn btn--ghost" style="left:132px;top:71px;width:115px"><svg width="20" height="20" viewBox="0 0 20 20"><circle cx="10" cy="10" r="8" fill="none" stroke="#6a4ca3" stroke-width="1.3"/><path d="M6 10h8" stroke="#6a4ca3" stroke-width="1.3"/></svg>Withdraw</div>
      <div class="slot-box">
        <div class="small-label" style="left:30px;top:16px">Date</div>
        <div class="field" style="left:30px;top:37px;width:466px;height:42px">3/19/2026<svg width="18" height="18" viewBox="0 0 18 18"><rect x="2" y="3" width="14" height="13" rx="1.5" fill="none" stroke="#333" stroke-width="1.2"/><path d="M2 7h14M6 1v4M12 1v4" stroke="#333" stroke-width="1.2"/></svg></div>
        <div class="small-label" style="left:30px;top:94px">From</div>
        <div class="field" style="left:30px;top:117px;width:225px;height:42px">9:30 AM<svg width="18" height="18" viewBox="0 0 20 20"><circle cx="10" cy="10" r="8" fill="none" stroke="#333" stroke-width="1.4"/><path d="M10 5v5l3 2" fill="none" stroke="#333" stroke-width="1.4"/></svg></div>
        <div class="small-label" style="left:271px;top:94px">To</div>
        <div class="field" style="left:271px;top:117px;width:225px;height:42px">12:30 AM<svg width="18" height="18" viewBox="0 0 20 20"><circle cx="10" cy="10" r="8" fill="none" stroke="#333" stroke-width="1.4"/><path d="M10 5v5l3 2" fill="none" stroke="#333" stroke-width="1.4"/></svg></div>
        <div class="small-label" style="left:35px;top:177px;font-size:13.5px;line-height:17px">Current Assignment<br><b style="font-weight:500">No Assignment</b></div>
        <div class="abs" style="left:177px;top:177px;width:2px;height:38px;background:#999"></div>
        <div class="status" style="left:203px;top:181px"><span class="lead"><svg width="17" height="17" viewBox="0 0 20 20"><circle cx="10" cy="10" r="8" fill="none" stroke="#5aaa1e" stroke-width="1.5"/><path d="M10 5v5l3 2" fill="none" stroke="#5aaa1e" stroke-width="1.5"/></svg>Status</span><span class="tag tag--active">Active</span></div>
      </div>
      <div class="btn btn--purple" style="left:174px;top:389px;width:100px">Save</div>
      <div class="btn btn--dark" style="left:288px;top:389px;width:100px">Close</div>
    </div>
  </section>

</div>
</body>
</html>
```